Card Design Project

A simple, funky, cool birth announcement card
Not corporate, but arty
Not childish nor girlish
No baby pictures

Text is tbc (eg name and date may change)

Front side: just the name "fenna"
Should be easy to read

Back side text (in Dutch):

We vinden je nu al leuk!

14 JUNE 2013
Penang

Dochter van Marieke Dorrel & Joost Vermalen

Mandalay, Myanmar
+95 1 64 8319
Skype: Marieke.Dorrel
Skype: Joost.Vermalen

Size will be A6
Updates

Reason: Dear designers, At this stage we would like to have one or more designers to draft up the card (of which the final text is still tbd as the baby is yet to be born) using the typeface used on the left below (or similar!) of the newly added picture - in black - in fluorescent colours Can you get back to us in a few days? Thanks

Target Market(s)

Our funky friends in holland.

Industry/Entity Type

Baby

Requirements
Must have
• Colours, aswe are very happy to welcome this baby.
Something that makes it stand out from all other baby birth announcement cards

A6 size
Deadline 21 June
Printing will be on white (thick paper 250g)
Design for 5mm "bleedsides" all around
At least available in PDF (and other formats)
Nice to have
• We've recently moved from netherlands to Mandalay
We could include the iconic kyauktaran pagoda

I would like for it to look like a cool party announcement

Include bright fluoriscent colours, including orange.
The enveloppe will be orange
Should not have
• Any baby stuff, soft pink dominance, childish stuff.

```html
<!DOCTYPE html>
<html lang="nl">
<head>
<meta charset="utf-8">
<title>Geboortekaart fenna</title>
<link rel="stylesheet" href="https://fonts.googleapis.com/css2?family=Mouse+Memoirs&display=swap">
<style>
  :root {
    --backdrop: #262626;
    --paper: #ffffff;
    --purple: #b0108f;
    --orange: #ff6a00;
    --orange-bright: #ff7f0f;
    --red: #ff2a45;
    --green: #2fd12a;
    --cyan: #25e6f0;
    --blue: #2a8fe8;
    --magenta: #f0148c;
    --letter-red: #ff1f4b;
    --letter-orange: #ff8c1a;
    --letter-green: #22cc3a;
    --letter-blue: #1a7fe6;
  }

  * { box-sizing: border-box; margin: 0; padding: 0; }

  html, body {
    width: 1200px;
    height: 900px;
    overflow: hidden;
    background: var(--backdrop);
  }

  .canvas {
    position: relative;
    width: 1200px;
    height: 900px;
    font-family: "Mouse Memoirs", "Arial Narrow", sans-serif;
    text-transform: uppercase;
    letter-spacing: 0.5px;
  }

  /* Front of the card */
  .card-front {
    position: absolute;
    left: 476px;
    top: 20px;
    width: 700px;
    height: 496px;
    background: var(--paper);
  }

  .card-front .name-lettering {
    position: absolute;
    left: 84px;
    top: 18px;
    width: 564px;
    height: 458px;
    border-radius: 10px;
    background:
      linear-gradient(to bottom, rgba(255,255,255,0) 0%, rgba(255,255,255,0) 48%, rgba(255,255,255,0.35) 52%, rgba(255,255,255,0.35) 100%),
      linear-gradient(to right, var(--letter-red) 0%, var(--letter-orange) 30%, var(--letter-green) 62%, var(--letter-blue) 100%);
  }

  .card-front .base-band {
    position: absolute;
    left: 0;
    bottom: 0;
    width: 100%;
    height: 18px;
    background: var(--purple);
  }

  /* Back of the card */
  .card-back {
    position: absolute;
    left: 20px;
    top: 370px;
    width: 724px;
    height: 490px;
    background: var(--paper);
  }

  .card-back .greeting-band {
    height: 72px;
    background: var(--purple);
    color: var(--paper);
    font-size: 40px;
    font-weight: 400;
    line-height: 72px;
    padding-left: 36px;
  }

  .card-back .details {
    padding: 16px 36px 0;
  }

  .birth-date { color: var(--green); font-size: 34px; line-height: 44px; }
  .birth-place { color: var(--magenta); font-size: 34px; line-height: 44px; }

  .parents {
    margin-top: 24px;
    font-size: 46px;
    line-height: 52px;
    white-space: nowrap;
  }
  .parents .intro { color: var(--red); }
  .parents .mother { color: var(--green); }
  .parents .amp { color: var(--orange); }
  .parents .father { color: var(--cyan); }

  .contact {
    list-style: none;
    margin-top: 20px;
    font-size: 28px;
  }
  .contact li { line-height: 32px; margin-bottom: 16px; }
  .contact .city { color: var(--blue); }
  .contact .phone { color: var(--red); }
  .contact .skype-mother { color: var(--green); }
  .contact .skype-father { color: var(--purple); }

  .card-back .base-band {
    position: absolute;
    left: 0;
    bottom: 0;
    width: 100%;
    height: 16px;
    background: var(--orange-bright);
  }
</style>
</head>
<body>
<main class="canvas">

  <section class="card-front" aria-label="Voorkant">
    <div class="name-lettering" role="img" aria-label="Hand-lettered name 'fenna' in bright red, orange, green and blue strokes with a faded mirrored reflection below"></div>
    <div class="base-band"></div>
  </section>

  <section class="card-back" aria-label="Achterkant">
    <h1 class="greeting-band">We vinden je nu al leuk!</h1>
    <div class="details">
      <p class="birth-date">14 June 2013</p>
      <p class="birth-place">Penang</p>
      <p class="parents">
        <span class="intro">Dochter van</span>
        <span class="mother">Marieke Dorrel</span>
        <span class="amp">&amp;</span>
        <span class="father">Joost Vermalen</span>
      </p>
      <ul class="contact">
        <li class="city">Mandalay, Myanmar</li>
        <li class="phone">+95 1 64 8319</li>
        <li class="skype-mother">Skype: Marieke.Dorrel</li>
        <li class="skype-father">Skype: Joost.Vermalen</li>
      </ul>
    </div>
    <div class="base-band"></div>
  </section>

</main>
</body>
</html>
```